lantern pathway for children needs a website designer

We need a website designer for our new extension to our company known as 'lantern pathway' providing shadow support services to children based in Singapore. We are a sister branch of a private clinic 'Bright horizons' providing speech language, occupational, and educational therapy to children.

We would like to use our own photos. So the selected design should have a frame with pictures to give us an idea but we will replace them with our own. We will be needing help with inputting information and changing information throughout.

We would like to see designs that are simple, and professional. We have a logo (see attached). The result should convey professionalism in shadow support, fostering independent thinking and moving students towards self-learning.

Target Market(s)

Teachers, psychologists, parents

Industry/Entity Type

Clinic

Requirements
Should not have
• too distracting colours

```html
<!DOCTYPE html>
<html lang="en">
<head>
<meta charset="utf-8">
<title>Lantern Pathway — Shadow Support</title>
<link rel="stylesheet" href="https://fonts.googleapis.com/css2?family=Oswald:wght@300;400&family=Lato:wght@300;400&family=Open+Sans:wght@400&display=swap">
<style>
  :root {
    --navy: #1f3350;
    --navy-bar: #34465d;
    --navy-line: #4d5f76;
    --page: #e7ebee;
    --crimson: #7b0a0a;
    --crimson-dark: #640404;
    --ink: #2a3a52;
    --text: #3f4650;
    --white: #ffffff;
    --field: #ebedee;
    --field-line: #c7cbcf;
    --accordion: #e4e9ee;
    --accordion-line: #b9c3cf;
  }
  * { box-sizing: border-box; margin: 0; padding: 0; }
  html, body { width: 1000px; height: 1200px; overflow: hidden; }
  body { position: relative; background: var(--page); font-family: "Lato", sans-serif; color: var(--text); }
  .abs { position: absolute; }

  .topbar { left: 0; top: 0; width: 1000px; height: 36px; background: var(--navy-bar); border-bottom: 1px solid var(--navy-line); color: #d6dde6; font-family: "Open Sans", sans-serif; font-size: 10px; }
  .topbar .item { position: absolute; top: 14px; display: flex; align-items: center; gap: 5px; }
  .topbar .auth { left: 517px; color: #fff; font-size: 10px; }
  .topbar .social { left: 678px; top: 12px; display: flex; gap: 6px; }
  .topbar .social span { width: 11px; height: 11px; border-radius: 50%; background: #9aa7b7; display: block; }
  .topbar .search { left: 755px; top: 11px; width: 94px; height: 15px; border: 1px solid #aab5c3; border-radius: 8px; font-size: 7px; color: #aab5c3; padding: 2px 0 0 15px; }

  .header { left: 0; top: 36px; width: 1000px; height: 65px; background: var(--navy); }
  .brand { left: 152px; top: 56px; display: flex; align-items: center; gap: 8px; font-family: "Oswald", sans-serif; font-weight: 400; font-size: 24px; color: #e9ecef; letter-spacing: .5px; }
  .brand .dot { width: 14px; height: 14px; border-radius: 50%; background: var(--crimson); }
  .nav { left: 464px; top: 72px; font-family: "Oswald", sans-serif; font-weight: 300; font-size: 13.5px; color: #c9d3df; }
  .nav a { position: absolute; white-space: nowrap; color: inherit; text-decoration: none; }
  .nav a.current { color: #fff; }
  .nav .chev { font-size: 9px; vertical-align: 1px; }

  .hero-photo { left: 150px; top: 101px; width: 700px; height: 264px; background: linear-gradient(100deg, #d9dfe3 0%, #eef0ee 35%, #e2c9bc 55%, #d7b39c 70%, #9fc492 100%); }
  .hero-band { left: 150px; top: 365px; width: 700px; height: 59px; background: var(--crimson); color: #f3e3e3; font-family: "Oswald", sans-serif; font-weight: 300; font-size: 11px; line-height: 21.5px; }
  .hero-band p { position: absolute; left: 20px; top: 7px; width: 440px; }
  .hero-band .arrows { position: absolute; left: 480px; top: 22px; display: flex; gap: 8px; }
  .hero-band .more { position: absolute; left: 559px; top: 0; width: 141px; height: 59px; background: var(--crimson-dark); color: #fff; font-size: 11px; display: flex; align-items: center; justify-content: center; }
  .hero-shade { left: 150px; top: 424px; width: 700px; height: 22px; background: radial-gradient(ellipse 50% 100% at 50% 0, rgba(0,0,0,.28), rgba(0,0,0,0)); }

  .section-title { left: 160px; width: 680px; display: flex; align-items: center; gap: 14px; font-family: "Oswald", sans-serif; font-weight: 400; color: var(--ink); font-size: 22px; }
  .section-title::before, .section-title::after { content: ""; flex: 1; height: 1px; background: #c8ced4; }
  .welcome-copy { left: 155px; top: 494px; width: 690px; text-align: center; font-family: "Oswald", sans-serif; font-weight: 300; font-size: 10.4px; line-height: 17px; color: #2f353d; }
  .welcome-copy p + p { margin-top: 6px; }

  .service-card { top: 630px; width: 215px; height: 87px; background: var(--white); box-shadow: 0 1px 3px rgba(0,0,0,.25); display: flex; align-items: center; justify-content: center; text-align: center; padding: 0 9px; font-weight: 300; font-size: 10.2px; line-height: 17px; color: #3f444a; }
  .service-card::after { content: ""; position: absolute; right: 0; top: 0; border-style: solid; border-width: 0 8px 8px 0; border-color: transparent var(--page) #d5d9dd transparent; }

  .block-title { top: 757px; display: flex; align-items: center; gap: 8px; font-family: "Oswald", sans-serif; font-weight: 400; font-size: 16px; color: var(--ink); }
  .block-title::before, .block-title::after { content: ""; flex: 1; height: 1px; background: #c8ced4; }

  .panel { top: 786px; height: 275px; background: var(--white); box-shadow: 0 1px 3px rgba(0,0,0,.25); }
  .acc-row { position: absolute; left: 7px; width: 440px; height: 29px; background: var(--accordion); border: 1px solid var(--accordion-line); font-family: "Oswald", sans-serif; font-weight: 300; font-size: 14px; color: #4e6177; padding: 4px 0 0 9px; }
  .acc-row .toggle { position: absolute; right: 0; top: -1px; width: 33px; height: 29px; border: 1px solid var(--accordion-line); display: flex; align-items: center; justify-content: center; }
  .acc-body { position: absolute; left: 16px; top: 45px; width: 422px; font-family: Arial, sans-serif; font-size: 9.2px; line-height: 14.4px; color: #222; }
  .acc-body .indent { text-indent: 93px; }
  .acc-body ul { list-style: none; margin: 0 0 0 100px; }
  .acc-body li { line-height: 20px; }
  .acc-body li::before { content: "✓ "; color: var(--crimson); }

  .field { position: absolute; left: 15px; width: 184px; height: 27px; background: var(--field); border: 1px solid var(--field-line); font-family: "Oswald", sans-serif; font-weight: 300; font-size: 10px; color: #a6acb3; padding: 6px 0 0 8px; }
  .register-btn { position: absolute; left: 56px; top: 216px; width: 100px; height: 24px; border-radius: 4px; background: var(--crimson); color: #fff; font-family: "Oswald", sans-serif; font-weight: 300; font-size: 11px; display: flex; align-items: center; justify-content: center; }

  .footer { left: 0; top: 1090px; width: 1000px; height: 110px; background: var(--navy); color: #fff; font-family: "Oswald", sans-serif; font-weight: 300; }
  .footer h4 { position: absolute; top: 12px; font-weight: 400; font-size: 11px; }
  .footer .subscribe { position: absolute; left: 150px; top: 43px; width: 188px; height: 31px; border: 1px solid #3a5a86; border-radius: 3px; background: #1a2c46; }
  .footer .subscribe span { position: absolute; left: 9px; top: 10px; font-size: 6.5px; color: #7f8ea3; }
  .footer .subscribe b { position: absolute; right: 10px; top: 6px; font-weight: 300; font-size: 13px; }
  .footer .links { position: absolute; left: 409px; top: 46px; font-size: 8.5px; color: #e3e8ee; }
  .footer .circles { position: absolute; left: 647px; top: 38px; display: flex; gap: 15px; }
  .footer .circles span { width: 28px; height: 28px; border-radius: 50%; background: #fff; display: block; }
  .footer .copy { position: absolute; left: 0; width: 1002px; top: 96px; text-align: center; font-family: "Open Sans", sans-serif; font-size: 6.5px; color: #dfe5ec; }
</style>
</head>
<body>

<div class="abs topbar">
  <div class="item" style="left:152px">
    <svg width="10" height="9" viewBox="0 0 10 9"><path d="M1 3 Q5 0 9 3 L8 4 L6.5 3 L3.5 3 L2 4 Z M2.5 4.5 H7.5 L8.5 8.5 H1.5 Z" fill="#c7d0db"/></svg>
    +65 6000 1234
  </div>
  <div class="item" style="left:256px">
    <svg width="13" height="9" viewBox="0 0 13 9"><rect x=".5" y=".5" width="12" height="8" fill="none" stroke="#c7d0db"/><path d="M.5 .5 L6.5 5 L12.5 .5" fill="none" stroke="#c7d0db"/></svg>
    hello@brightfield-comm.sg
  </div>
  <div class="item auth">Register &nbsp;|&nbsp; login</div>
  <div class="item social"><span></span><span></span><span></span></div>
  <div class="abs search">
    <svg class="abs" style="left:4px;top:2px" width="8" height="8" viewBox="0 0 8 8"><circle cx="3.2" cy="3.2" r="2.4" fill="none" stroke="#aab5c3"/><path d="M5 5 L7.5 7.5" stroke="#aab5c3"/></svg>
    Search here...
  </div>
</div>

<div class="abs header"></div>
<div class="abs brand"><span class="dot"></span>Lantern Pathway</div>
<nav class="abs nav">
  <a class="current" style="left:0">HOME</a>
  <a style="left:52px">ABOUT US</a>
  <a style="left:123px">SERVICES <span class="chev">▾</span></a>
  <a style="left:192px">SUPPORT</a>
  <a style="left:259px">BLOG</a>
  <a style="left:309px">CONTACT US</a>
</nav>

<div class="abs hero-photo" role="img" aria-label="Photo of a therapist playing with a young child using finger puppets"></div>
<div class="abs hero-band">
  <p>Provide families with well-trained Shadows who are mentored by Speech Language Pathologists and Professional Therapists to carry out shadow support.</p>
  <div class="arrows">
    <svg width="12" height="12" viewBox="0 0 12 12"><circle cx="6" cy="6" r="6" fill="#5a0606"/><path d="M7 3 L4 6 L7 9" fill="none" stroke="#ddd" stroke-width="1.6"/></svg>
    <svg width="12" height="12" viewBox="0 0 12 12"><circle cx="6" cy="6" r="6" fill="#5a0606"/><path d="M5 3 L8 6 L5 9" fill="none" stroke="#ddd" stroke-width="1.6"/></svg>
  </div>
  <div class="more">READ MORE</div>
</div>
<div class="abs hero-shade"></div>

<h2 class="abs section-title" style="top:449px">WELCOME TO OUR WEBSITE</h2>
<div class="abs welcome-copy">
  <p>Lantern Pathway is part of the Brightfield Communication Group of Companies, who are providing speech language therapy, occupational therapy and educational therapy services to both the Singapore and the international school community.</p>
  <p>Lantern Pathway aims to work in an integrated manner, respecting the work of the respective professionals involved and collaborating effectively.</p>
</div>

<h2 class="abs section-title" style="top:575px;font-size:19px">OUR SERVICES</h2>
<div class="abs service-card" style="left:150px">Train shadows with a strong focus on equipping them with dynamic, clinical skills.</div>
<div class="abs service-card" style="left:392px">Provide families with well-trained Shadows who are mentored by Speech Language Pathologists and Professional Therapists to carry out shadow support.</div>
<div class="abs service-card" style="left:636px">Work with educational professionals (Educational Psychologists) to provide an effective solution to the learning needs of a student.</div>

<h3 class="abs block-title" style="left:150px;width:457px">SHADOW SUPPORT</h3>
<h3 class="abs block-title" style="left:636px;width:215px">QUICK REGISTER</h3>

<div class="abs panel" style="left:150px;width:457px">
  <div class="acc-row" style="top:7px">What is shadow support?
    <span class="toggle"><svg width="16" height="16" viewBox="0 0 16 16"><circle cx="8" cy="8" r="7.5" fill="var(--crimson)"/><rect x="4" y="7" width="8" height="2" fill="#fff"/></svg></span>
  </div>
  <div class="acc-body">
    <p class="indent">A shadow support is para-professional who can help a struggling student to integrate and learn in their school environment. &nbsp; At different points in a student's life, there may be a need for a para-professional who could step in to help make a difference. &nbsp; Students who need shadows are those who:</p>
    <ul>
      <li>Have difficulties in integrating learning in classroom</li>
      <li>Have social challenges and find it difficult to connect with peers</li>
      <li>Have difficulties in understanding instructions</li>
    </ul>
    <p class="indent">A central goal of the shadow support would be to help the student achieve independence in their learning journey eventually.</p>
  </div>
  <div class="acc-row" style="top:203px">What are its Advantages?
    <span class="toggle"><svg width="16" height="16" viewBox="0 0 16 16"><circle cx="8" cy="8" r="7.5" fill="var(--crimson)"/><rect x="4" y="7" width="8" height="2" fill="#fff"/><rect x="7" y="4" width="2" height="8" fill="#fff"/></svg></span>
  </div>
  <div class="acc-row" style="top:236px">How do I know if my child needs shadowing?
    <span class="toggle"><svg width="16" height="16" viewBox="0 0 16 16"><circle cx="8" cy="8" r="7.5" fill="var(--crimson)"/><rect x="4" y="7" width="8" height="2" fill="#fff"/><rect x="7" y="4" width="2" height="8" fill="#fff"/></svg></span>
  </div>
</div>

<div class="abs panel" style="left:636px;width:215px">
  <div class="field" style="top:22px">Enter Your Name</div>
  <div class="field" style="top:67px">Enter Your mail Address</div>
  <div class="field" style="top:115px">Phone</div>
  <div class="field" style="top:164px">Zip Code</div>
  <div class="register-btn">REGISTER</div>
</div>

<footer class="abs footer">
  <h4 style="left:152px">SUBSCRIBE TO NEWSLETTER</h4>
  <div class="subscribe"><span>Enter Your email Address</span><b>SUBMIT</b></div>
  <h4 style="left:394px">QUICK LINKS</h4>
  <div class="links">Site map | about us | contact us | Privacy policy</div>
  <h4 style="left:644px;top:14px">STAY CONNECTED</h4>
  <div class="circles"><span></span><span></span><span></span></div>
  <div class="copy">Copyright© 2014 · All rights reserved</div>
</footer>

</body>
</html>
```